Brenwick Coaching Website

I would like someone to design my website. I have an existing site which is really basic and needs an overhaul. I have attached a powerpoint with all the information I require. I am flexible with the design and layout and am ok with graphics being added to enhance the attractiveness of the site.

```html
<!DOCTYPE html>
<html lang="en">
<head>
<meta charset="utf-8">
<title>Brenwick Coaching</title>
<link rel="stylesheet" href="https://fonts.googleapis.com/css2?family=Open+Sans:wght@400;600&display=swap">
<style>
:root{
  --page:#ffffff;
  --brand-blue:#1a73c4;
  --nav-top:#1e88d8;
  --nav-bottom:#1469b4;
  --panel:#f6f6f6;
  --panel-line:#e2e2e2;
  --text:#333333;
  --muted:#4a4a4a;
  --photo-a:#6f7a6c;
  --photo-b:#c9c2b3;
  --social:#5a6f8a;
}
*{margin:0;padding:0;box-sizing:border-box}
html,body{width:1200px;height:744px;overflow:hidden;background:var(--page)}
body{position:relative;font-family:"Open Sans",Arial,sans-serif;color:var(--text)}
.brand{position:absolute;left:54px;top:50px;display:flex;align-items:center;gap:10px;
  font-size:30px;font-weight:400;color:var(--brand-blue);letter-spacing:.5px}
.brand-dot{width:14px;height:14px;border-radius:50%;background:var(--brand-blue)}
.contact{position:absolute;left:878px;font-size:16px;color:#222;display:flex;align-items:center;gap:13px}
.contact svg{width:22px;height:18px;fill:var(--brand-blue)}
.contact.phone{top:43px}
.contact.email{top:79px}
.site-nav{position:absolute;left:57px;top:143px;width:254px}
.site-nav a{display:flex;align-items:center;height:90px;margin-bottom:13px;padding-left:28px;
  background:linear-gradient(var(--nav-top),var(--nav-bottom));color:#fff;text-decoration:none;
  font-size:16px;font-weight:600}
.site-nav a.short{height:63px}
.intro{position:absolute;left:343px;top:142px;width:802px;height:401px;background:var(--panel);border:1px solid var(--panel-line)}
.intro h1{position:absolute;left:31px;top:22px;font-size:28px;font-weight:400;color:var(--brand-blue)}
.intro p{position:absolute;left:31px;top:82px;width:443px;font-size:13px;line-height:32px;text-align:justify;color:var(--text)}
.profile{position:absolute;left:527px;top:23px;width:252px;height:363px;background:#fafafa;border:1px solid var(--panel-line)}
.profile-photo{position:absolute;left:4px;top:4px;width:242px;height:299px;background:linear-gradient(160deg,var(--photo-b),var(--photo-a))}
.profile-name{position:absolute;left:29px;top:318px;font-size:21px;color:#333}
.offer{position:absolute;left:343px;top:562px;width:802px;height:55px;background:var(--panel);border:1px solid var(--panel-line);
  display:flex;align-items:center;padding-left:31px;font-size:14px;color:var(--muted)}
.site-footer{position:absolute;left:57px;top:641px;width:1088px;height:86px;background:var(--panel);border:1px solid var(--panel-line);
  display:flex;align-items:center;justify-content:space-between;padding:0 25px 0 27px;font-size:14px;color:var(--muted)}
.social{display:flex;gap:8px}
.social span{width:27px;height:27px;border-radius:50%;background:var(--social)}
</style>
</head>
<body>
<header>
  <div class="brand"><span class="brand-dot"></span>Brenwick Coaching</div>
  <div class="contact phone">
    <svg viewBox="0 0 22 18" aria-hidden="true"><path d="M2 6c0-3 5-4 9-4s9 1 9 4v2h-5V6c-1-1-7-1-8 0v2H2z"/><rect x="4" y="9" width="14" height="8" rx="2"/></svg>
    1300 555 274
  </div>
  <div class="contact email">
    <svg viewBox="0 0 22 18" aria-hidden="true"><path d="M1 2h20v14H1z"/><path d="M1 2l10 8 10-8" fill="none" stroke="#fff" stroke-width="1.5"/></svg>
    Maren.Hale@brenwickcoaching.com
  </div>
</header>
<nav class="site-nav">
  <a href="#">Individual Coaching (1)</a>
  <a href="#">Group Work (2)</a>
  <a href="#">Resources (3)</a>
  <a href="#">Inspiration Booth (5)</a>
  <a href="#" class="short">Inspiration Booth (5)</a>
</nav>
<main>
  <section class="intro">
    <h1>Brenwick Coaching</h1>
    <p>Welcome to Brenwick Coaching where we put a new perspective on the way you work, live and play.&nbsp; Through our programs you will learn new skills &amp; techniques to enable you to break through the barriers that have kept you from reaching your full potential up to now. Welcome to Brenwick Coaching where we put a new perspective on the way you work, live and play.&nbsp; Through our programs you will learn new skills &amp; techniques to enable you to break through the barriers that have kept you from reaching your full potential up to now.</p>
    <div class="profile">
      <div class="profile-photo" role="img" aria-label="Portrait photo of coach Maren outdoors among trees"></div>
      <div class="profile-name">About&nbsp; Maren</div>
    </div>
  </section>
  <div class="offer">Get your free 30 minute introductory coaching session... (4)</div>
</main>
<footer class="site-footer">
  <span>©2014 Brenwick Coaching, All Rights Reserved.</span>
  <div class="social" aria-label="Social links"><span></span><span></span><span></span><span></span></div>
</footer>
</body>
</html>
```